New Zealand Marlborough Sauvignon Blanc wine packaging design

We need packaging design for our new wine brand, Dunmore Vale. The wine is a New Zealand Marlborough Sauvignon Blanc. We would like the packaging will portray elegance and style with an understated label. We are looking for a label that portrays the elegance of the French Riviera. The label should be round or pill shaped.
Updates

Industry/Entity Type

Wine

Font styles to use
Serif
Sans Serif

Requirements
Must have
• The words in order of importance: Dunmore Vale, Sauvignon Blanc, Marlborough, New Zealand. It should be fit to the bottle posted in the links
Nice to have
• a pill shape or circular shape
Should not have
• Illustrations of wine bottles, wine glasses, or grapes

```html
<!DOCTYPE html>
<html lang="en">
<head>
<meta charset="utf-8">
<title>Dunmore Vale Sauvignon Blanc Label</title>
<link rel="stylesheet" href="https://fonts.googleapis.com/css2?family=Josefin+Sans:wght@300;400;600&display=swap">
<style>
  :root {
    --paper: #ffffff;
    --ring-top: #6c5363;
    --ring-bottom: #918491;
    --sky-glow: #fff8fb;
    --sky-pink: #f3b8cf;
    --ridge-lilac: #b49ac0;
    --ridge-plum: #8a4b6e;
    --ridge-deep: #3a1518;
    --water-mist: #a99096;
    --title-ink: #7a5a6b;
    --caption-ink: #3b2a33;
    --varietal-ink: #f4ecf0;
  }
  * { box-sizing: border-box; margin: 0; padding: 0; }
  html, body {
    width: 1200px;
    height: 675px;
    overflow: hidden;
    background: var(--paper);
  }
  .canvas {
    position: relative;
    width: 1200px;
    height: 675px;
    background: var(--paper);
    font-family: "Josefin Sans", "Futura", sans-serif;
  }
  .label {
    position: absolute;
    left: 350px;
    top: 87px;
    width: 500px;
    height: 500px;
  }
  .label-art {
    position: absolute;
    inset: 0;
    width: 500px;
    height: 500px;
  }
  .brand-name {
    position: absolute;
    left: 113px;
    top: 124px;
    width: 274px;
    font-weight: 600;
    font-size: 37px;
    line-height: 42px;
    color: var(--title-ink);
  }
  .brand-line {
    display: flex;
    justify-content: space-between;
  }
  .varietal {
    position: absolute;
    left: 0;
    width: 500px;
    top: 349px;
    text-align: center;
    font-weight: 300;
    font-size: 13px;
    letter-spacing: 12.4px;
    padding-left: 12px;
    color: var(--varietal-ink);
  }
  .region {
    position: absolute;
    left: 0;
    width: 500px;
    top: 479px;
    text-align: center;
    font-weight: 400;
    font-size: 10.5px;
    letter-spacing: 0.2px;
    color: var(--caption-ink);
  }
</style>
</head>
<body>
<main class="canvas">
  <section class="label">
    <svg class="label-art" viewBox="0 0 500 500" aria-hidden="false">
      <defs>
        <linearGradient id="ring-fill" x1="0" y1="0" x2="0" y2="1">
          <stop offset="0" stop-color="var(--ring-top)"/>
          <stop offset="1" stop-color="var(--ring-bottom)"/>
        </linearGradient>
        <linearGradient id="band-fill" x1="0" y1="0" x2="0" y2="1">
          <stop offset="0" stop-color="var(--ridge-lilac)"/>
          <stop offset="0.2" stop-color="var(--ridge-plum)"/>
          <stop offset="0.38" stop-color="var(--ridge-deep)"/>
          <stop offset="0.62" stop-color="var(--ridge-deep)"/>
          <stop offset="0.8" stop-color="var(--ridge-plum)"/>
          <stop offset="1" stop-color="var(--ridge-lilac)"/>
        </linearGradient>
        <linearGradient id="scene-fill" x1="0" y1="0" x2="0" y2="1">
          <stop offset="0" stop-color="var(--sky-glow)"/>
          <stop offset="0.3" stop-color="var(--sky-pink)"/>
          <stop offset="0.42" stop-color="var(--ridge-lilac)"/>
          <stop offset="0.52" stop-color="#8e6670"/>
          <stop offset="0.6" stop-color="var(--ridge-deep)"/>
          <stop offset="0.7" stop-color="var(--water-mist)"/>
          <stop offset="0.8" stop-color="var(--ridge-lilac)"/>
          <stop offset="0.9" stop-color="var(--sky-pink)"/>
          <stop offset="1" stop-color="var(--sky-glow)"/>
        </linearGradient>
        <clipPath id="outer-disc">
          <circle cx="250" cy="250" r="250"/>
        </clipPath>
      </defs>
      <circle class="label-ring" cx="250" cy="250" r="250" fill="url(#ring-fill)"/>
      <rect class="label-band" x="0" y="180" width="500" height="221"
            fill="url(#band-fill)" clip-path="url(#outer-disc)"
            role="img" aria-label="Layered mountain ridges at dusk continuing across the border ring"/>
      <circle class="label-scene" cx="250" cy="250" r="198" fill="url(#scene-fill)"
              role="img" aria-label="Illustrated dusk landscape of lilac and plum mountain ridges reflected in a still lake under a glowing pink sky"/>
    </svg>
    <h1 class="brand-name">
      <span class="brand-line"><span>D</span><span>U</span><span>N</span><span>M</span><span>O</span><span>R</span><span>E</span></span>
      <span class="brand-line"><span>V</span><span>A</span><span>L</span><span>E</span></span>
    </h1>
    <p class="varietal">SAUVIGNON BLANC</p>
    <p class="region">MARLBOROUGH, NEW ZEALAND</p>
  </section>
</main>
</body>
</html>
```